SOLVE Study flyer

I need help designing a flyer for a research study that will include brain imaging in adolescents. The info is in the attached document. The study is called the Sequoia Outlook Lantern Valley Echo (SOLVE) study. Ideally this would be returned as a document that I can edit in the future as we will have several new recruitment phases (different age groups, etc. I also would love to have a logo designed as part of this project, but I recognize that might be a separate design request.

```html
<!DOCTYPE html>
<html lang="en">
<head>
<meta charset="UTF-8">
<title>SOLVE Study Flyer</title>
<link href="https://fonts.googleapis.com/css2?family=Poppins:wght@300;400;500;600;700;800&display=swap" rel="stylesheet">
<style>
  :root {
    --navy: #1f1760;
    --purple: #5a3e9e;
    --violet: #8d6bcb;
    --lilac: #b9a3e3;
    --card: #efedf6;
    --gold: #f2b924;
    --ink: #3a3848;
    --paper: #ffffff;
    --backdrop: #d6d6d8;
    --rule: #d8d3e8;
  }
  * { box-sizing: border-box; margin: 0; padding: 0; }
  html, body { width: 1200px; height: 900px; overflow: hidden; }
  body {
    background: var(--backdrop);
    font-family: "Poppins", sans-serif;
    color: var(--ink);
    position: relative;
  }
  .flyer {
    position: absolute; left: 290px; top: 20px;
    width: 620px; height: 860px;
    background: var(--paper);
    overflow: hidden;
    box-shadow: 0 10px 30px rgba(0,0,0,.18);
  }
  .hero { position: absolute; right: 0; top: 0; width: 380px; height: 400px; }
  .hero svg { width: 100%; height: 100%; display: block; }

  .brand { position: absolute; left: 34px; top: 120px; display: flex; align-items: center; gap: 16px; }
  .brand-mark { width: 70px; height: 70px; border-radius: 50%; background: var(--violet); }
  .brand-name { font-size: 52px; font-weight: 300; color: var(--navy); line-height: 1; letter-spacing: 1px; }
  .brand-full {
    font-size: 10px; font-weight: 400; color: var(--navy); text-transform: uppercase;
    line-height: 1.3; letter-spacing: .5px; margin-top: 4px;
    border-bottom: 1.5px solid var(--gold); padding-bottom: 4px; width: 200px;
  }

  .headline {
    position: absolute; left: 34px; top: 250px; width: 320px;
    font-size: 23px; font-weight: 800; line-height: 1.18; color: var(--navy);
  }
  .headline em { font-style: normal; color: var(--purple); display: block; }
  .headline::after { content: ""; display: block; width: 48px; height: 3px; background: var(--gold); margin-top: 12px; }

  .intro {
    position: absolute; left: 34px; top: 385px; width: 290px;
    font-size: 11px; line-height: 1.55; color: var(--ink);
  }
  .intro strong { color: var(--purple); font-weight: 600; }

  .card {
    position: absolute; background: var(--card); border-radius: 14px; padding: 18px 18px 12px 24px;
  }
  .card-title {
    font-size: 11.5px; font-weight: 600; color: var(--purple); text-transform: uppercase;
    letter-spacing: .3px; line-height: 1.35; margin-bottom: 8px; padding-left: 26px;
  }
  .card-badge {
    position: absolute; left: -16px; top: 12px; width: 34px; height: 34px; border-radius: 50%;
    background: var(--paper); border: 2px solid var(--purple);
    display: flex; align-items: center; justify-content: center;
  }
  .participation { left: 30px; top: 466px; width: 292px; }
  .eligibility { left: 340px; top: 385px; width: 255px; height: 240px; padding-top: 22px; }
  .eligibility .card-badge { background: var(--navy); border-color: var(--navy); top: 14px; }

  .steps, .criteria { list-style: none; }
  .steps li {
    display: flex; gap: 12px; align-items: flex-start; padding: 5px 0;
    border-top: 1px solid var(--rule); font-size: 9px; line-height: 1.35;
  }
  .steps li:first-child { border-top: none; padding-top: 0; }
  .step-icon {
    flex: 0 0 30px; height: 30px; border-radius: 50%; background: var(--violet);
    display: flex; align-items: center; justify-content: center;
  }
  .steps b { display: block; font-size: 10.5px; font-weight: 600; color: var(--purple); }

  .criteria li {
    display: flex; gap: 12px; align-items: center; padding: 10px 0;
    border-top: 1px solid var(--rule); font-size: 11px; line-height: 1.35;
  }
  .criteria li:first-child { border-top: none; }
  .criteria .hl { color: var(--purple); font-weight: 600; }
  .criteria .age { font-size: 22px; font-weight: 700; color: var(--navy); display: block; line-height: 1.1; }
  .tick { flex: 0 0 18px; height: 18px; }

  .band {
    position: absolute; left: 0; top: 700px; width: 620px; height: 100px; background: var(--navy);
    display: flex; align-items: center; padding: 0 30px; gap: 16px;
  }
  .band-icon {
    flex: 0 0 52px; height: 52px; border-radius: 50%; background: var(--violet);
    display: flex; align-items: center; justify-content: center;
  }
  .contact { flex: 1; color: #fff; font-size: 10.5px; line-height: 1.4; }
  .contact .lead { color: var(--gold); font-weight: 600; text-transform: uppercase; font-size: 11.5px; }
  .email {
    display: inline-block; margin-top: 6px; background: var(--gold); color: var(--navy);
    font-weight: 700; font-size: 11.5px; padding: 4px 16px; border-radius: 20px;
  }
  .divider { width: 1px; height: 56px; background: rgba(255,255,255,.35); }
  .compensation { color: var(--gold); line-height: 1; }
  .compensation .label { font-size: 11px; font-weight: 600; text-transform: uppercase; }
  .compensation .upto { font-size: 9px; color: #fff; text-transform: uppercase; }
  .compensation .amount { font-size: 44px; font-weight: 800; }

  .footer { position: absolute; right: 34px; top: 812px; display: flex; align-items: center; gap: 10px; }
  .footer-mark { width: 26px; height: 26px; background: var(--navy); }
  .footer-name { font-size: 17px; font-weight: 600; color: var(--navy); }
</style>
</head>
<body>
<main class="flyer">
  <div class="hero">
    <svg viewBox="0 0 380 400" preserveAspectRatio="none">
      <defs>
        <linearGradient id="heroFill" x1="0" y1="0" x2="1" y2="1">
          <stop offset="0" stop-color="#c9b5ec"/>
          <stop offset=".55" stop-color="#9676d0"/>
          <stop offset="1" stop-color="#4b3690"/>
        </linearGradient>
      </defs>
      <path d="M60 0 H380 V340 H150 C70 300 20 180 30 90 C34 50 44 20 60 0 Z" fill="var(--lilac)"/>
      <path d="M70 0 H380 V340 H160 C85 300 34 180 42 92 C46 52 56 22 70 0 Z" fill="#3f2f86"/>
      <path d="M100 30 H380 V400 H150 C110 340 80 200 100 30 Z" fill="url(#heroFill)" role="img" aria-label="Photo of a thoughtful teenage girl in a lavender sweatshirt, resting her chin on her hand, with a faint brain graphic behind her"/>
    </svg>
  </div>

  <div class="brand">
    <div class="brand-mark"></div>
    <div>
      <div class="brand-name">SOLVE</div>
      <div class="brand-full">Sequoia Outlook Lantern<br>Valley Echo Study</div>
    </div>
  </div>

  <h1 class="headline">Are you the parent of a child age 10–17?
    <em>Do they worry or overthink negative emotions?</em></h1>

  <p class="intro">Northgate University researchers are seeking <strong>girls age 10–17</strong> for a study about brain activity in emotions and decision-making and how they relate to puberty, anxiety and depression.</p>

  <section class="card participation">
    <span class="card-badge">
      <svg width="16" height="16" viewBox="0 0 16 16"><circle cx="8" cy="4.5" r="3" fill="var(--purple)"/><path d="M2 15 C2 10 14 10 14 15 Z" fill="var(--purple)"/></svg>
    </span>
    <h2 class="card-title">Study participation involves:</h2>
    <ul class="steps">
      <li><span class="step-icon"><svg width="16" height="16" viewBox="0 0 16 16" fill="none" stroke="#fff" stroke-width="1.4"><rect x="2" y="2" width="12" height="12" rx="2"/><path d="M5 6h6M5 9h4"/></svg></span>
        <span><b>One one-hour interview</b>(online or in-person) where your child will discuss their thoughts</span></li>
      <li><span class="step-icon"><svg width="16" height="16" viewBox="0 0 16 16" fill="none" stroke="#fff" stroke-width="1.4"><rect x="3" y="1.5" width="10" height="13" rx="1.5"/><path d="M5.5 5h5M5.5 8h5M5.5 11h3"/></svg></span>
        <span><b>Online questionnaires</b>(parent and child)</span></li>
      <li><span class="step-icon"><svg width="16" height="16" viewBox="0 0 16 16" fill="none" stroke="#fff" stroke-width="1.4"><path d="M2 13 V8 a6 6 0 0 1 12 0 V13 Z"/><circle cx="8" cy="9" r="2.5"/></svg></span>
        <span><b>One two-hour visit</b>where your child will complete an MRI scan, answer questions about their puberty stage, and have a small hair sample taken to study puberty hormones</span></li>
    </ul>
  </section>

  <section class="card eligibility">
    <span class="card-badge">
      <svg width="14" height="14" viewBox="0 0 14 14"><path d="M5 1h4v4h4v4H9v4H5V9H1V5h4z" fill="#fff"/></svg>
    </span>
    <h2 class="card-title">Your child may be eligible if they:</h2>
    <ul class="criteria">
      <li><svg class="tick" viewBox="0 0 18 18" fill="none" stroke="var(--gold)" stroke-width="1.6"><circle cx="9" cy="9" r="7.5"/><path d="M5.5 9.2l2.4 2.4 4.6-5"/></svg>
        <span>Are age <span class="age">10–17</span></span></li>
      <li><svg class="tick" viewBox="0 0 18 18" fill="none" stroke="var(--gold)" stroke-width="1.6"><circle cx="9" cy="9" r="7.5"/><path d="M5.5 9.2l2.4 2.4 4.6-5"/></svg>
        <span>Tend to <span class="hl">worry or overthink</span> negative thoughts</span></li>
      <li><svg class="tick" viewBox="0 0 18 18" fill="none" stroke="var(--gold)" stroke-width="1.6"><circle cx="9" cy="9" r="7.5"/><path d="M5.5 9.2l2.4 2.4 4.6-5"/></svg>
        <span>Have not been diagnosed with psychosis, learning problems, or autism</span></li>
    </ul>
  </section>

  <section class="band">
    <span class="band-icon">
      <svg width="26" height="20" viewBox="0 0 26 20" fill="none" stroke="#fff" stroke-width="1.6"><rect x="1" y="1" width="24" height="18" rx="2"/><path d="M1 2l12 9 12-9"/></svg>
    </span>
    <div class="contact">
      <div class="lead">Interested in participating?</div>
      Want more information? Please contact us!<br>
      <span class="email">solvestudy@northgate.edu</span>
    </div>
    <span class="divider"></span>
    <span class="band-icon">
      <svg width="24" height="22" viewBox="0 0 24 22" fill="none" stroke="#fff" stroke-width="1.6"><rect x="2" y="8" width="20" height="13" rx="1"/><rect x="1" y="5" width="22" height="4"/><path d="M12 5v16M12 5C9 1 5 2 7 5M12 5c3-4 7-3 5 0"/></svg>
    </span>
    <div class="compensation">
      <div class="label">Compensation</div>
      <div class="upto">up to</div>
      <div class="amount">$140</div>
    </div>
  </section>

  <footer class="footer">
    <span class="footer-mark"></span>
    <span class="footer-name">Northgate University</span>
  </footer>
</main>
</body>
</html>
```